Modern Business Card for Larkwell 2018

Our company assumes the best about people. We are creating an online community of entrepreneurs and business leaders who struggle with marketing their business online.

This business card should POP! We recently got a new logo and are launching a new website next month, so our business cards should make a statement that feels:
-Fresh
-Smart
-Trustworthy
-Fun

Target Market(s)

small business owners, entrepreneurs

Industry/Entity Type

Digital Marketing

Contact Information for Business Card

Dimensions: 3.5" x 2"

Font styles to use
Sans Serif

Colors
f37122
ffffff

Requirements
Must have
• We need a business card with a modern, bold design. We will use one side of the card as a lead-generation offer, so text on one side will need to fit up to 140 characters. The business card should stick to our core colors (orange, black, and white).
Nice to have
• We think a vertical "portrait" design could be interesting.
Should not have
• Should not look like a traditional business card. The round icon should stand out from a distance.

```html
<!DOCTYPE html>
<html lang="en">
<head>
<meta charset="utf-8">
<title>Larkwell Business Card</title>
<link href="https://fonts.googleapis.com/css2?family=Open+Sans:wght@400;600;700;800&display=swap" rel="stylesheet">
<style>
  :root {
    --orange: #f37122;
    --orange-deep: #e4601a;
    --white: #ffffff;
    --ink: #1e1e1e;
    --field: #e9e9e9;
    --backdrop: #d9d9d9;
  }
  * { margin: 0; padding: 0; box-sizing: border-box; }
  html, body { width: 1200px; height: 960px; overflow: hidden; }
  body {
    background: var(--backdrop);
    font-family: "Open Sans", Arial, sans-serif;
    position: relative;
  }
  .card {
    position: absolute;
    left: 250px;
    width: 700px;
    height: 400px;
    border-radius: 4px;
    overflow: hidden;
    box-shadow: 0 6px 18px rgba(0,0,0,.18);
  }
  /* Offer side */
  .card--offer { top: 50px; background: var(--orange); color: var(--white); }
  .brand {
    position: absolute; left: 40px; top: 70px; width: 270px;
    text-align: center;
  }
  .brand__dot {
    display: block; width: 46px; height: 46px; margin: 0 auto 12px;
    border-radius: 50%; background: var(--white);
  }
  .brand__name {
    font-weight: 800; font-size: 52px; letter-spacing: 2px; line-height: 1;
    text-transform: uppercase;
  }
  .brand__tagline {
    margin-top: 10px; font-weight: 700; font-size: 12.5px;
    letter-spacing: 2.4px; text-transform: uppercase;
  }
  .divider {
    position: absolute; left: 340px; top: 40px; width: 1px; height: 180px;
    background: rgba(255,255,255,.55);
  }
  .offer {
    position: absolute; left: 370px; top: 38px; width: 300px;
  }
  .offer__headline {
    font-weight: 800; font-size: 21px; line-height: 1.05; text-transform: uppercase;
  }
  .offer__body {
    margin-top: 10px; font-size: 16px; line-height: 1.25;
  }
  .offer__url {
    margin-top: 12px; font-weight: 700; font-size: 19px;
  }
  .write-in {
    position: absolute; left: 40px; right: 30px; top: 250px; height: 110px;
    background: var(--field); border-radius: 18px;
  }
  .write-in__line {
    position: absolute; left: 30px; right: 30px; height: 1px; background: #555;
  }
  .write-in__line--one { top: 38px; }
  .write-in__line--two { top: 74px; }

  /* Contact side */
  .card--contact { top: 510px; background: var(--white); }
  .contact-band {
    position: absolute; left: 0; bottom: 0; width: 330px; height: 190px;
  }
  .contact {
    position: absolute; left: 34px; bottom: 44px; color: var(--white);
  }
  .contact__name { font-weight: 700; font-size: 26px; text-transform: uppercase; line-height: 1.1; }
  .contact__role { font-weight: 700; font-size: 19px; text-transform: uppercase; margin-top: 4px; }
  .contact__email { font-size: 19px; margin-top: 2px; }
  .mark {
    position: absolute; right: 70px; top: 90px;
    display: flex; flex-direction: column; align-items: center; gap: 14px;
  }
  .mark__dot {
    width: 150px; height: 150px; border-radius: 50%; background: var(--orange);
  }
  .mark__name {
    font-weight: 800; font-size: 24px; letter-spacing: 2px;
    color: var(--orange); text-transform: uppercase;
  }
</style>
</head>
<body>

  <section class="card card--offer" aria-label="Offer side">
    <div class="brand">
      <span class="brand__dot"></span>
      <div class="brand__name">Larkwell</div>
      <div class="brand__tagline">Tell stories that inspire action</div>
    </div>
    <div class="divider"></div>
    <div class="offer">
      <p class="offer__headline">Reach more people.<br>Make more money.<br>Create more impact.</p>
      <p class="offer__body">Get your free Larkwell Starter Package and our marketing guide today at</p>
      <p class="offer__url">Larkwellnow.com/start</p>
    </div>
    <div class="write-in">
      <span class="write-in__line write-in__line--one"></span>
      <span class="write-in__line write-in__line--two"></span>
    </div>
  </section>

  <section class="card card--contact" aria-label="Contact side">
    <svg class="contact-band" viewBox="0 0 330 190" preserveAspectRatio="none">
      <polygon points="0,0 280,0 330,190 0,190" fill="var(--orange)"/>
    </svg>
    <div class="contact">
      <p class="contact__name">Dana Whitfield</p>
      <p class="contact__role">Story Marketing Coach</p>
      <p class="contact__email">dana@larkwellnow.com</p>
    </div>
    <div class="mark">
      <span class="mark__dot"></span>
      <span class="mark__name">Larkwell</span>
    </div>
  </section>

</body>
</html>
```